Concierge Healthcare Business Card Design and Logo

We need a logo and business card design for a new company called "Sound Haven". We will provide concierge audiological care, hearing aids, hearing exams, custom hearing protection etc to patients in the comfort of their homes and offices. We would like a sleek and modern design preferably with an Ear related logo.

Target Market(s)

People with hearing loss, Hunters, Musicians
My usual clientele are older individuals so usually 50+ years old

Industry/Entity Type

Health Care

Contact Information for Business Card

Celia Brandt, AuD
Audiologist
512-648-2917
soundhaven@mailvoro.com
www.soundhaven-vorel.com

Logo Text

Sound Haven

Number of Pages Required

3 page

```html
<!DOCTYPE html>
<html lang="en">
<head>
<meta charset="utf-8">
<title>Sound Haven — Business Card</title>
<link rel="stylesheet" href="https://fonts.googleapis.com/css2?family=PT+Sans:wght@400&display=swap">
<style>
  :root {
    --backdrop: #3b3430;
    --card: #101010;
    --card-edge: #1a1a1a;
    --brand-blue: #1e9bc9;
    --brand-green: #7cb82f;
    --ink: #f2f2f2;
    --rule: #3a3a3a;
  }
  * { margin: 0; padding: 0; box-sizing: border-box; }
  html, body {
    width: 1200px; height: 844px; overflow: hidden;
    background: var(--backdrop);
    font-family: "PT Sans", "Helvetica Neue", Arial, sans-serif;
  }
  .canvas {
    position: relative; width: 1200px; height: 844px;
    display: flex; align-items: center; justify-content: center; gap: 50px;
  }
  .card {
    position: relative; width: 525px; height: 300px;
    background: var(--card);
    border: 1px solid var(--card-edge);
    box-shadow: 0 12px 30px rgba(0,0,0,.45);
  }
  .brand {
    position: absolute; display: flex; align-items: center; gap: 12px;
    color: var(--brand-blue); font-size: 38px; font-weight: 400; letter-spacing: .5px;
  }
  .brand-dot {
    width: 22px; height: 22px; border-radius: 50%; background: var(--brand-green);
  }
  .card-front .brand { left: 130px; top: 62px; }
  .card-back .brand { left: 50%; top: 50%; transform: translate(-50%, -50%); font-size: 42px; }

  .person {
    position: absolute; right: 290px; top: 176px; text-align: right; color: var(--ink);
  }
  .person-name { font-size: 21px; line-height: 1.1; }
  .person-name .first { color: var(--brand-blue); }
  .person-name .last { color: var(--brand-green); }
  .person-role { font-size: 14px; margin-top: 2px; }
  .person-address { font-size: 14px; line-height: 1.2; margin-top: 12px; }

  .divider {
    position: absolute; left: 250px; top: 170px; width: 1px; height: 88px; background: var(--rule);
  }
  .contact {
    position: absolute; left: 268px; top: 170px; list-style: none; color: var(--ink);
  }
  .contact li {
    display: flex; align-items: center; gap: 9px; font-size: 13.5px; line-height: 21px;
  }
  .contact svg { width: 11px; height: 11px; fill: var(--brand-blue); flex: none; }
</style>
</head>
<body>
<main class="canvas">
  <section class="card card-front">
    <div class="brand"><span class="brand-dot"></span>Sound Haven</div>

    <div class="person">
      <p class="person-name"><span class="first">Celia</span> <span class="last">Brandt</span></p>
      <p class="person-role">Managing Director</p>
      <p class="person-address">12345, Address Goes Here<br>Country Name, 123456</p>
    </div>

    <div class="divider"></div>

    <ul class="contact">
      <li>
        <svg viewBox="0 0 24 24" aria-hidden="true"><path d="M6.6 10.8a15.1 15.1 0 0 0 6.6 6.6l2.2-2.2c.3-.3.7-.4 1-.2 1.1.4 2.3.6 3.6.6.6 0 1 .4 1 1V20c0 .6-.4 1-1 1C10.6 21 3 13.4 3 4c0-.6.4-1 1-1h3.5c.6 0 1 .4 1 1 0 1.2.2 2.4.6 3.6.1.3 0 .7-.2 1z"/></svg>
        512-648-2917
      </li>
      <li>
        <svg viewBox="0 0 24 24" aria-hidden="true"><path d="M6 2h12v5H6zM3 8h18a1 1 0 0 1 1 1v8h-4v5H6v-5H2V9a1 1 0 0 1 1-1zm5 7v5h8v-5z"/></svg>
        512-648-2918
      </li>
      <li>
        <svg viewBox="0 0 24 24" aria-hidden="true"><path d="M2 5h20v14H2zm2 2v.5l8 5 8-5V7l-8 5z"/></svg>
        soundhaven@mailvoro.com
      </li>
      <li>
        <svg viewBox="0 0 24 24" aria-hidden="true"><path d="M12 2a10 10 0 1 0 0 20 10 10 0 0 0 0-20zm-1 3v3H8a8 8 0 0 1 3-3zm2 0a8 8 0 0 1 3 3h-3zM5 10h6v4H5a8 8 0 0 1 0-4zm8 0h6a8 8 0 0 1 0 4h-6zm-5 6h3v3a8 8 0 0 1-3-3zm5 0h3a8 8 0 0 1-3 3z"/></svg>
        www.soundhaven-vorel.com
      </li>
    </ul>
  </section>

  <section class="card card-back">
    <div class="brand"><span class="brand-dot"></span>Sound Haven</div>
  </section>
</main>
</body>
</html>
```